Coffee House With Cycling Theme Wants Business Cards

We want to create a business card for a coffee house that has a cycling theme. We expect to use the current logo on one side of the business card and we have been considering adding the words 'COFFEE HOUSE' underneath (see example). For the other side of the business card we want an interesting design with tag-line, address and social media links (the normal business card stuff). See examples provided but we are not fixed on having it exactly as shown, we are very open to great creative ideas. Please note our logo has the initials ‘KR' in orange embedded in the design and this must be retained. However, you can play with the words COFFEE HOUSE as well as use the orange color on the backside of the business card, as you see fit. For an image on the backside of the business card it can be a photo, hand-drawn or whatever but it must visually combine coffee and cycling in some way. The interior of the Coffee House will be reclaimed wood, rustic and have an urban feel to it with cycling artifacts hanging from the walls/ceiling, etc. Finally, it would be beneficial if the business card design elements can be easily used on flyers and other promotional assets. Good luck, we are looking forward to seeing your creative ideas.

Target Market(s)

Coffee lovers and cycling fans

Contact Information for Business Card

See project description.

Colors

Designer to choose colors to be used in the design.

Requirements
Must have
• Must use the current logo provided and combine a coffee and bike theme.
Nice to have
• Orange is used in current logo and could be used as an accent color on the backside of the business card.

```html
<!DOCTYPE html>
<html lang="en">
<head>
<meta charset="utf-8">
<title>KR Coffee House – Business Cards</title>
<link rel="stylesheet" href="https://fonts.googleapis.com/css2?family=Lato:wght@400;700&display=swap">
<style>
  :root {
    --canvas: #d4d4d4;
    --card-light: #efefef;
    --charcoal: #3d3d3d;
    --orange: #ff6a1f;
    --white: #ffffff;
    --text-dark: #3a3a3a;
    --bean-brown: #8a5234;
    --road-dark: #3b3e3d;
  }
  * { margin: 0; padding: 0; box-sizing: border-box; }
  html, body { width: 1200px; height: 1200px; overflow: hidden; }
  body {
    background: var(--canvas);
    font-family: "Lato", sans-serif;
    position: relative;
  }
  .card {
    position: absolute;
    top: 310px;
    width: 364px;
    height: 594px;
    overflow: hidden;
    box-shadow: 0 3px 6px rgba(0,0,0,0.35);
  }
  .card--front { left: 234px; background: var(--card-light); }
  .card--back { left: 643px; width: 370px; }

  /* Front */
  .brand-name {
    position: absolute;
    top: 130px; left: 0; width: 100%;
    text-align: center;
    font-size: 64px; font-weight: 400; line-height: 1;
    color: var(--text-dark);
  }
  .front-title {
    position: absolute; top: 246px; width: 100%; text-align: center;
    font-size: 36px; font-weight: 400; color: var(--orange); line-height: 1;
  }
  .front-url {
    position: absolute; top: 289px; width: 100%; text-align: center;
    font-size: 20px; color: var(--text-dark); line-height: 1;
  }
  .tagline-band {
    position: absolute; top: 363px; left: 0; width: 100%; height: 113px;
    background: var(--charcoal); text-align: center;
  }
  .tagline-band__main {
    margin-top: 26px; font-size: 33px; font-weight: 700; color: var(--orange);
    line-height: 1; letter-spacing: -0.3px;
  }
  .tagline-band__sub {
    margin-top: 9px; font-size: 20px; font-weight: 700; color: var(--white); line-height: 1;
  }
  .address-band {
    position: absolute; top: 476px; left: 0; width: 100%; height: 118px;
    background: var(--orange); color: var(--white); text-align: center;
    font-size: 18px; font-weight: 700; line-height: 24px; padding-top: 28px;
  }

  /* Back */
  .back-visual {
    position: absolute; inset: 0;
    background: linear-gradient(180deg, #9a5a3a 0%, var(--bean-brown) 35%, #4a3a32 55%, var(--road-dark) 75%, #434645 100%);
  }
  .back-name {
    position: absolute; top: 240px; left: 0; width: 100%;
    text-align: center;
    font-size: 64px; font-weight: 400; line-height: 1; color: var(--white);
  }
  .social {
    position: absolute; left: 40px; top: 486px;
    display: flex; flex-direction: column; align-items: center;
  }
  .social__dot {
    width: 34px; height: 34px; border-radius: 50%; background: var(--white);
  }
  .social__handle {
    margin-top: 10px; font-size: 20px; color: var(--white); line-height: 1.2;
  }
</style>
</head>
<body>
  <section class="card card--front">
    <p class="brand-name">KR</p>
    <h1 class="front-title">COFFEE HOUSE</h1>
    <p class="front-url">www.krcoffeehouse.com</p>
    <div class="tagline-band">
      <p class="tagline-band__main">BEANS &amp; BIKES</p>
      <p class="tagline-band__sub">GET YOUR DAILY QUOTA</p>
    </div>
    <div class="address-band">
      <p>501, Address Goes Here</p>
      <p>Country Name, 123456</p>
    </div>
  </section>

  <section class="card card--back">
    <div class="back-visual" role="img" aria-label="Roasted coffee beans above a road cyclist riding toward the viewer"></div>
    <p class="back-name">KR</p>
    <div class="social">
      <span class="social__dot"></span>
      <span class="social__handle">krcoffeehouse</span>
    </div>
  </section>
</body>
</html>
```